Stylish new business card needed!

Hello everyone! I am in need of a new business card design for an alarm company here in Hurricane WV. I have all fonts, color codes and logos provided for you use! We are a young company and like the style of a clean sleek looking business card. Would like it double sided, one side holding the logo and the other with your design!
Target Market(s)
The people that are looking for the newest tech for home automation and security
Industry/Entity Type
Alarm services; Home automation
Contact Information for Business Card
Name of person; position (Sales; Installer); Phone Number (555.418.7260); Employee cell Number; Website (www.GuardedByVelk.example); Employee Email; Double sided
Look and feel
Each slider illustrates characteristics of the customer's brand and the style your logo design should communicate.

```html
<!DOCTYPE html>
<html lang="en">
<head>
<meta charset="utf-8">
<title>Velk Business Card</title>
<link href="https://fonts.googleapis.com/css2?family=Lato:wght@400;700;900&display=swap" rel="stylesheet">
<style>
  :root {
    --backdrop: #2b2d31;
    --card-white: #ffffff;
    --card-grey: #999999;
    --brand-orange: #f58634;
    --text-grey: #8a8a8a;
    --light: #ffffff;
  }
  * { box-sizing: border-box; margin: 0; padding: 0; }
  html, body { width: 1200px; height: 952px; overflow: hidden; }
  body {
    background: var(--backdrop);
    font-family: 'Lato', sans-serif;
    display: flex;
    flex-direction: column;
    align-items: center;
    justify-content: center;
    gap: 56px;
  }
  .card {
    width: 600px;
    height: 343px;
    border-radius: 22px;
    position: relative;
    overflow: hidden;
  }
  .card-front { background: var(--card-white); }
  .card-back { background: var(--card-grey); display: flex; align-items: center; justify-content: center; }

  .wordmark { display: flex; align-items: center; gap: 10px; }
  .wordmark-dot { width: 14px; height: 14px; border-radius: 50%; background: var(--brand-orange); }
  .wordmark-name { font-weight: 900; letter-spacing: 2px; text-transform: uppercase; color: var(--brand-orange); }

  .card-front .wordmark { position: absolute; left: 44px; top: 46px; }
  .card-front .wordmark-name { font-size: 26px; color: var(--text-grey); }

  .card-back .wordmark-name { font-size: 44px; color: var(--light); }
  .card-back .wordmark-dot { width: 22px; height: 22px; }

  .contact-list { position: absolute; left: 44px; top: 150px; list-style: none; }
  .contact-item { display: flex; align-items: center; gap: 10px; font-size: 13.5px; color: var(--text-grey); margin-bottom: 9px; }
  .contact-icon { width: 16px; height: 16px; border-radius: 3px; background: var(--brand-orange); display: flex; align-items: center; justify-content: center; }
  .contact-icon svg { width: 11px; height: 11px; }

  .person { position: absolute; right: 44px; top: 170px; text-align: right; }
  .person-name { font-size: 22px; color: var(--brand-orange); letter-spacing: 1px; text-transform: uppercase; }
  .person-name strong { font-weight: 900; }
  .person-role { font-size: 16px; color: var(--text-grey); margin-top: 4px; }
  .person-rule { width: 62px; height: 2px; background: var(--brand-orange); margin: 10px 0 0 auto; }
</style>
</head>
<body>
  <section class="card card-front">
    <div class="wordmark">
      <span class="wordmark-dot"></span>
      <span class="wordmark-name">Guarded by Velk</span>
    </div>
    <ul class="contact-list">
      <li class="contact-item">
        <span class="contact-icon"><svg viewBox="0 0 12 12"><path d="M3 1l2 2.5-1.2 1.2a6 6 0 0 0 3.5 3.5L8.5 7 11 9l-1.5 2A9 9 0 0 1 1 2.5z" fill="#fff"/></svg></span>
        555.418.7260
      </li>
      <li class="contact-item">
        <span class="contact-icon"><svg viewBox="0 0 12 12"><rect x="1" y="2.5" width="10" height="7" fill="none" stroke="#fff" stroke-width="1.2"/><path d="M1 2.5l5 4 5-4" fill="none" stroke="#fff" stroke-width="1.2"/></svg></span>
        hello@guardedbyvelk.example
      </li>
      <li class="contact-item">
        <span class="contact-icon"><svg viewBox="0 0 12 12"><circle cx="6" cy="6" r="4.5" fill="none" stroke="#fff" stroke-width="1.2"/><path d="M1.5 6h9M6 1.5c-2 3-2 6 0 9M6 1.5c2 3 2 6 0 9" fill="none" stroke="#fff" stroke-width="1"/></svg></span>
        www.GuardedByVelk.example
      </li>
    </ul>
    <div class="person">
      <p class="person-name">Daniel R. <strong>Marsh</strong></p>
      <p class="person-role">Managing Director</p>
      <div class="person-rule"></div>
    </div>
  </section>

  <section class="card card-back">
    <div class="wordmark">
      <span class="wordmark-dot"></span>
      <span class="wordmark-name">Guarded by Velk</span>
    </div>
  </section>
</body>
</html>
```